Parcelwise HQ letterhead and envelope

Design a formal (8.5x11) letterhead and envelope for sales outreach and legal matters. Using design input from https://www.parcelwisehq.example/ and the attached documents.

Industry/Entity Type

Software Service

Requirements
Must have
• These 4 hex colors are our official colors:
• #355c98 [blue]
• #1eb1a2 [teal]
• #fdba12 [gold]
• #f1653b [orange]
• So no other colors besides these should be used.

```html
<!DOCTYPE html>
<html lang="en">
<head>
<meta charset="utf-8">
<title>Parcelwise HQ Letterhead</title>
<link href="https://fonts.googleapis.com/css2?family=Lato:wght@400;700&family=Arimo:wght@400&family=Kaushan+Script&display=swap" rel="stylesheet">
<style>
  :root {
    --brand-blue: #355c98;
    --ink: #3b3b3b;
    --ink-dark: #1f1f1f;
    --paper-top: #ffffff;
    --paper-bottom: #f1f1f1;
    --rule: #b9b9b9;
  }
  * { margin: 0; padding: 0; box-sizing: border-box; }
  html, body { width: 974px; height: 1200px; overflow: hidden; }
  body { background: var(--paper-top); }
  .letterhead {
    position: relative;
    width: 974px; height: 1200px;
    overflow: hidden;
    background: linear-gradient(160deg, var(--paper-top) 35%, var(--paper-bottom) 100%);
    font-family: "Lato", sans-serif;
    color: var(--ink);
  }
  .brand {
    position: absolute; left: 83px; top: 36px;
    display: flex; align-items: center; gap: 14px;
  }
  .brand-dot {
    width: 44px; height: 44px; border-radius: 50%;
    border: 4px solid var(--brand-blue);
  }
  .brand-name {
    font-family: "Lato", sans-serif; font-weight: 400;
    font-size: 38px; color: var(--brand-blue); letter-spacing: 0.5px;
  }
  .address {
    position: absolute; left: 721px; top: 40px;
    border-left: 1px solid var(--rule);
    padding-left: 14px;
    font-family: "Arimo", sans-serif; font-style: normal;
    font-size: 15.5px; line-height: 18px;
    color: var(--ink-dark);
  }
  .address-line { display: flex; align-items: center; gap: 4px; }
  .address-line.indent { padding-left: 18px; }
  .salutation {
    position: absolute; left: 83px; top: 228px;
    font-weight: 700; font-size: 17.5px; color: var(--brand-blue);
  }
  .body-copy {
    position: absolute; left: 83px; width: 808px;
    font-size: 18.2px; line-height: 27.6px; color: var(--ink);
  }
  .body-copy .line { display: block; text-align: justify; text-align-last: justify; white-space: nowrap; }
  .body-copy .line.last { text-align-last: left; }
  .p1 { top: 270px; } .p2 { top: 427px; } .p3 { top: 583px; }
  .closing {
    position: absolute; left: 83px; top: 755px;
    font-size: 22px; color: var(--ink-dark);
  }
  .signature {
    position: absolute; left: 83px; top: 790px;
    font-family: "Kaushan Script", cursive; font-size: 36px; color: var(--brand-blue);
  }
  .contacts {
    position: absolute; left: 83px; top: 1087px;
    list-style: none;
    font-family: "Arimo", sans-serif; font-size: 15.5px; color: var(--ink-dark);
  }
  .contacts li { display: flex; align-items: center; gap: 6px; height: 24.5px; }
  .contacts svg { width: 15px; height: 15px; flex: none; }
  .backdrop-ring { position: absolute; left: 500px; top: 740px; width: 490px; height: 490px; }
</style>
</head>
<body>
<main class="letterhead">
  <svg class="backdrop-ring" viewBox="0 0 490 490" aria-hidden="true">
    <circle cx="244" cy="240" r="216" fill="none" stroke="#355c98" stroke-opacity="0.13" stroke-width="26"/>
  </svg>

  <header>
    <div class="brand">
      <span class="brand-dot"></span>
      <span class="brand-name">Parcelwise HQ</span>
    </div>
    <address class="address">
      <span class="address-line">
        <svg width="14" height="14" viewBox="0 0 14 14" aria-hidden="true"><circle cx="7" cy="7" r="6" fill="none" stroke="#355c98" stroke-width="1.2"/><path d="M7 3.2a2.4 2.4 0 0 1 2.4 2.4c0 1.8-2.4 4.4-2.4 4.4S4.6 7.4 4.6 5.6A2.4 2.4 0 0 1 7 3.2z" fill="#355c98"/><circle cx="7" cy="5.6" r="0.9" fill="#fff"/></svg>
        82 Cedar Fold Way
      </span>
      <span class="address-line indent">Elmdale, MI 49001</span>
    </address>
  </header>

  <p class="salutation">Dear Mr. Lorem,</p>

  <p class="body-copy p1">
    <span class="line">Lorem ipsum dolor sit amet, consectetuer adipiscing elit, sed diam nonummy nibh euismod tinci-</span>
    <span class="line">dunt ut laoreet dolore magna aliquam erat volutpat. Ut wisi enim ad minim veniam, quis nostrud</span>
    <span class="line">exerci tation ullamcorper suscipit lobortis nisl ut aliquip ex ea commodo consequat. Duis autem vel</span>
    <span class="line">eum iriure dolor in hendiusto odio dignissim qui blandit praesent luptatum zzril delenit augue duis</span>
    <span class="line last">dolore te feugait nulla facilisi.</span>
  </p>
  <p class="body-copy p2">
    <span class="line">Lorem ipsum dolor sit amet, consectetuer adipiscing elit, sed diam nonummy nibh euismod tinci-</span>
    <span class="line">dunt ut laoreet dolore magna aliquam erat volutpat. Ut wisi enim ad minim veniam, quis nostrud</span>
    <span class="line">exerci tation ullamcorper suscipit lobortis nisl ut aliquip ex ea commodo consequat. Duis autem vel</span>
    <span class="line">eum iriure dolor in hendiusto odio dignissim qui blandit praesent luptatum zzril delenit augue duis</span>
    <span class="line last">dolore te feugait nulla facilisi.</span>
  </p>
  <p class="body-copy p3">
    <span class="line">Lorem ipsum dolor sit amet, consectetuer adipiscing elit, sed diam nonummy nibh euismod tinci-</span>
    <span class="line">dunt ut laoreet dolore magna aliquam erat volutpat. Ut wisi enim ad minim veniam, quis nostrud</span>
    <span class="line">exerci tation ullamcorper suscipit lobortis nisl ut aliquip ex ea commodo consequat. Duis autem vel</span>
    <span class="line">eum iriure dolor in hendiusto odio dignissim qui blandit praesent luptatum zzril delenit augue duis</span>
    <span class="line last">dolore te feugait nulla facilisi.</span>
  </p>

  <p class="closing">Sincerely Your,</p>
  <p class="signature">Your Name</p>

  <ul class="contacts">
    <li>
      <svg viewBox="0 0 15 15" aria-hidden="true"><circle cx="7.5" cy="7.5" r="6.8" fill="none" stroke="#355c98" stroke-width="1.1"/><rect x="5.2" y="3.8" width="4.6" height="7.4" rx="0.8" fill="none" stroke="#355c98" stroke-width="1.1"/></svg>
      (555) 014-2288
    </li>
    <li>
      <svg viewBox="0 0 15 15" aria-hidden="true"><circle cx="7.5" cy="7.5" r="6.8" fill="none" stroke="#355c98" stroke-width="1.1"/><path d="M4.6 4.2l1.4-.4 1 2-.9.8c.5 1 1.2 1.7 2.2 2.2l.8-.9 2 1-.4 1.4c-3.3 0-6.1-2.8-6.1-6.1z" fill="#355c98"/></svg>
      (555) 019-4700(Main)
    </li>
    <li>
      <svg viewBox="0 0 15 15" aria-hidden="true"><circle cx="7.5" cy="7.5" r="6.8" fill="none" stroke="#355c98" stroke-width="1.1"/><rect x="4" y="5" width="7" height="5" fill="none" stroke="#355c98" stroke-width="1.1"/><path d="M4 5l3.5 3 3.5-3" fill="none" stroke="#355c98" stroke-width="1.1"/></svg>
      jsmith@parcelwisehq.example
    </li>
    <li>
      <svg viewBox="0 0 15 15" aria-hidden="true"><circle cx="7.5" cy="7.5" r="6.8" fill="none" stroke="#355c98" stroke-width="1.1"/><ellipse cx="7.5" cy="7.5" rx="3" ry="6.8" fill="none" stroke="#355c98" stroke-width="1"/><path d="M0.8 7.5h13.4M2 4.2h11M2 10.8h11" stroke="#355c98" stroke-width="1"/></svg>
      www.parcelwisehq.example
    </li>
  </ul>
</main>
</body>
</html>
```